Falkrin homes and renovations business card design.

Would like some new card designs utilizing my new logo that look professional. I am open to different colors on the logo or utilize the same ones we have. I like the original concept but would like to see some fresh ideas and build on what we have already done.

Target Market(s)

Custom home building industry, Real estate sales, Renovation projects.

Industry/Entity Type

Home Builder

Contact Information for Business Card

Falkrin Homes and Renovations
2871 96th Avenue
Marrowby, Northvale
T2R3W8
Home : 403- 718-4063 Cell: 403- 294-5170

My info is : Dax Falkrin, President and CEO
email: falkrinhomes@maildrop-example.net
Website: falkrinhomes-example.com
websit

Requirements
Must have
• Must Use my new logo design. I am open to different colors on the logo or utilize the same ones in the existing design. I can upload the original logo design if needed.

```html
<!DOCTYPE html>
<html lang="en">
<head>
<meta charset="utf-8">
<title>Falkrin Homes and Renovations – Business Card</title>
<link rel="stylesheet" href="https://fonts.googleapis.com/css2?family=Montserrat:wght@400;500;700&display=swap">
<style>
  :root {
    --backdrop: #2f3d47;
    --card: #1b1a1b;
    --card-edge: #d5415f;
    --gold: #c8922a;
    --gold-bright: #e8b422;
    --grey: #9a9a9a;
    --text-font: "Montserrat", sans-serif;
  }
  * { box-sizing: border-box; margin: 0; padding: 0; }
  html, body { width: 1200px; height: 738px; overflow: hidden; }
  body {
    background: var(--backdrop);
    font-family: var(--text-font);
    display: flex;
    align-items: center;
    justify-content: center;
    gap: 56px;
  }
  .card {
    width: 504px;
    height: 288px;
    background: var(--card);
    border-radius: 3px;
    box-shadow: 0 4px 0 var(--card-edge);
    position: relative;
  }
  .card-front {
    display: flex;
    align-items: center;
    justify-content: center;
  }
  .brand { display: flex; flex-direction: column; align-items: center; }
  .brand-name {
    color: var(--gold);
    font-weight: 500;
    text-transform: uppercase;
    line-height: 1;
  }
  .brand-tagline {
    color: var(--grey);
    font-weight: 500;
    text-transform: uppercase;
    line-height: 1.2;
  }
  .card-front .brand-name { font-size: 56px; letter-spacing: 1px; }
  .card-front .brand-tagline { font-size: 17px; letter-spacing: 0.5px; margin-top: 8px; }
  .card-back {
    display: flex;
    align-items: center;
    padding: 0 26px;
  }
  .card-back .brand { width: 210px; }
  .card-back .brand-name { font-size: 32px; }
  .card-back .brand-tagline { font-size: 9.5px; letter-spacing: 0.3px; margin-top: 5px; color: var(--gold); }
  .divider {
    width: 2px;
    height: 86px;
    background: var(--gold);
    margin: 0 22px;
    flex: none;
  }
  .contact { color: var(--grey); font-size: 9.5px; line-height: 1.35; }
  .contact-name { color: var(--gold-bright); font-weight: 700; font-size: 19px; letter-spacing: 0.5px; line-height: 1.1; }
  .contact-title { margin-bottom: 9px; }
  .contact-address { margin-bottom: 9px; }
  .contact-line { display: flex; align-items: center; gap: 6px; white-space: nowrap; }
  .contact-line svg { width: 9px; height: 9px; fill: none; stroke: var(--grey); stroke-width: 1.4; flex: none; }
</style>
</head>
<body>
  <section class="card card-front" aria-label="Business card front">
    <div class="brand">
      <p class="brand-name">Falkrin</p>
      <p class="brand-tagline">Homes and Renovations</p>
    </div>
  </section>

  <section class="card card-back" aria-label="Business card back">
    <div class="brand">
      <p class="brand-name">Falkrin</p>
      <p class="brand-tagline">Homes and Renovations</p>
    </div>
    <div class="divider"></div>
    <div class="contact">
      <p class="contact-name">Dax Falkrin</p>
      <p class="contact-title">President and CEO</p>
      <p class="contact-address">2871 96th Avenue<br>Marrowby, Northvale<br>T2R3W8</p>
      <p class="contact-line">
        <svg viewBox="0 0 10 10" aria-hidden="true"><rect x="1.5" y="1" width="7" height="8" rx="1"/></svg>
        403- 718-4063
      </p>
      <p class="contact-line">
        <svg viewBox="0 0 10 10" aria-hidden="true"><rect x="2.5" y="0.8" width="5" height="8.4" rx="1"/><line x1="4.3" y1="7.6" x2="5.7" y2="7.6"/></svg>
        403- 294-5170
      </p>
      <p class="contact-line">
        <svg viewBox="0 0 10 10" aria-hidden="true"><rect x="0.8" y="2" width="8.4" height="6" rx="0.6"/><polyline points="1,2.4 5,5.4 9,2.4"/></svg>
        falkrinhomes@maildrop-example.net
      </p>
      <p class="contact-line">
        <svg viewBox="0 0 10 10" aria-hidden="true"><circle cx="5" cy="5" r="4"/><line x1="1" y1="5" x2="9" y2="5"/><ellipse cx="5" cy="5" rx="1.8" ry="4"/></svg>
        falkrinhomes-example.com
      </p>
    </div>
  </section>
</body>
</html>
```